Business Cards for new orthopaedic surgery practice

My husband and I are starting our own orthopaedic surgery practice. We are looking for a business card that is uniform, but one will have my name/title and the other will have his. You can just create one design with my name on it for now. But when I choose your design as the winning design I will ask that you add another copy with his name/title.

We are looking for classy, simple, elite all in one. We like dark blues/a little gold/yellow. Something that goes with our logo. We want our logo incorporated. Here is all the info you need:
Business name: RV Bone & Vitality Center
Location: 38517 North Willowmere Ave
Palm Hollow, FL 33490
Phone: 954-218-4063
Fax: 954-582-7341
Email: info@myrvbonecare.example

Names: Lydia Vance, M.D.
Board Certified Hand and Upper Extremity Surgeon

Ebo Dansu, M.D.
Board Certified Hip & Knee Replacement/General Orthopaedic Surgeon

Can decide what you want to put on the back. Maybe a slogan:
Rooted in Care. Focused on You

I am just going to upload our logo. The only thing is if we select you as the winning design, the location, and phone numbers may change. We will need your help to update that once fully solidified.

Industry/Entity Type

Medical

Contact Information for Business Card

Colors
0054AA
0677BA
7BADD7
CADEEF
E8F1F8
0094D4
00A9DD
6FCCEA
C7EBF8
E9F6FB

Requirements
Must have
• class, appeal,
Should not have
• We want to air on the side of masculine if we are looking at masculine vs. feminine feel. But we still want it classy, sophisticated, and something we will love

```html
<!DOCTYPE html>
<html lang="en">
<head>
<meta charset="utf-8">
<title>RV Bone &amp; Vitality Center – Business Card</title>
<link href="https://fonts.googleapis.com/css2?family=Poppins:wght@400;500;600&display=swap" rel="stylesheet">
<style>
  :root {
    --page: #1b1c1f;
    --card: #263d8a;
    --card-deep: #1f3478;
    --accent: #1fb4e4;
    --soft: #5f79c8;
    --white: #ffffff;
  }
  * { box-sizing: border-box; margin: 0; padding: 0; }
  html, body { width: 1200px; height: 900px; overflow: hidden; }
  body {
    background: var(--page);
    font-family: "Poppins", sans-serif;
    color: var(--white);
    display: flex;
    flex-direction: column;
    align-items: center;
    justify-content: center;
    gap: 36px;
  }
  .card {
    position: relative;
    width: 700px;
    height: 400px;
    background: var(--card);
    box-shadow: 0 14px 30px rgba(0,0,0,.5);
    overflow: hidden;
  }
  /* front */
  .holder { position: absolute; left: 52px; top: 54px; }
  .holder-name { color: var(--accent); font-weight: 600; font-size: 24px; letter-spacing: .5px; }
  .holder-title { font-size: 15px; margin-top: 2px; }
  .divider { position: absolute; left: 52px; right: 52px; top: 150px; height: 1.5px; background: var(--white); }
  .contacts { position: absolute; left: 52px; top: 176px; list-style: none; font-size: 15px; line-height: 27px; }
  .contacts li { display: flex; align-items: center; gap: 10px; }
  .contacts svg { width: 14px; height: 14px; fill: var(--accent); flex: none; }
  .practice-mark {
    position: absolute; right: 52px; top: 46px;
    display: flex; align-items: center; gap: 12px;
    font-weight: 500; font-size: 19px; text-transform: uppercase; letter-spacing: 1.5px;
    line-height: 1.3; text-align: left;
  }
  .practice-mark .dot { width: 14px; height: 14px; border-radius: 50%; background: var(--white); flex: none; }
  .address { position: absolute; right: 52px; bottom: 44px; font-size: 16px; line-height: 26px; text-align: right; }
  /* back */
  .emblem-field {
    position: absolute; left: 50%; top: -20px; width: 360px; height: 440px; transform: translateX(-50%);
    background: radial-gradient(ellipse at 50% 35%, var(--card-deep) 0%, var(--card-deep) 45%, rgba(95,121,200,.35) 75%, transparent 100%);
    border-radius: 46% 46% 20% 20%;
  }
  .back-content { position: absolute; inset: 0; display: flex; flex-direction: column; align-items: center; justify-content: center; }
  .back-name { font-weight: 500; font-size: 36px; text-transform: uppercase; letter-spacing: 2.5px; line-height: 1.2; }
  .center-row { display: flex; align-items: center; gap: 16px; }
  .center-row .rule { width: 90px; height: 2px; background: var(--white); }
  .slogan { color: var(--accent); font-size: 17px; margin-top: 10px; }
</style>
</head>
<body>
  <section class="card card-front">
    <div class="holder">
      <p class="holder-name">Lydia Vance, M.D.</p>
      <p class="holder-title">Hand and Upper Extremity Surgery</p>
    </div>
    <div class="practice-mark">
      <span class="dot"></span>
      <span>RV Bone &amp;<br>Vitality<br>Center</span>
    </div>
    <div class="divider"></div>
    <ul class="contacts">
      <li><svg viewBox="0 0 24 24"><path d="M6.6 10.8a15 15 0 0 0 6.6 6.6l2.2-2.2a1 1 0 0 1 1-.25 11.4 11.4 0 0 0 3.6.57 1 1 0 0 1 1 1V20a1 1 0 0 1-1 1A17 17 0 0 1 3 4a1 1 0 0 1 1-1h3.5a1 1 0 0 1 1 1c0 1.25.2 2.45.57 3.6a1 1 0 0 1-.25 1z"/></svg>954-218-4063</li>
      <li><svg viewBox="0 0 24 24"><path d="M6 2h10v5H6zM3 8h18v10h-3v4H6v-4H3zm5 7v5h8v-5z"/></svg>954-582-7341</li>
      <li><svg viewBox="0 0 24 24"><path d="M2 5h20v14H2zm2 2v.5l8 5 8-5V7zm0 2.9V17h16V9.9l-8 5z"/></svg>info@myrvbonecare.example</li>
    </ul>
    <p class="address">38517 North Willowmere Ave<br>Palm Hollow, FL 33490</p>
  </section>

  <section class="card card-back">
    <div class="emblem-field" role="img" aria-label="Large tone-on-tone practice emblem with a leafy tree"></div>
    <div class="back-content">
      <p class="back-name">RV Bone &amp; Vitality</p>
      <div class="center-row">
        <span class="rule"></span>
        <p class="back-name">Center</p>
        <span class="rule"></span>
      </div>
      <p class="slogan">Grounded in Trust Built for You</p>
    </div>
  </section>
</body>
</html>
```